Business Cards Design for the electrical wholesaler: clean bold dynamic :)

We need a business card design that would follow our latest brand guidelines. As an electrical wholesaler we want to bring a fresh look and feel into the industry. The design should be clean bold and dynamic. It should come alive with the renewed energy of our green colour. Our grey colour should keep things balanced and complement the notion of maturity and responsibility. We employ Lato as a corporate font however are not bound by this font and we’re open to interpretation here.

Target Market(s)

Electrical contractors

Industry/Entity Type

Business

Contact Information for Business Card

Logo
Name & Surname: Halyna Dorosh
Job Title: Director of Marketing
Email: halya.dorosh@quillmail.example
Cell phone: XXX.XXX.XXXX
Address: 20517 - 87 Ave. Edmonton, AB, Canada. T6K 4N8
Business Phone: 780.555.0184
Website: www.brovix.example

Font styles to use
Other font styles liked:
• Lato

Requirements
Must have
• Logo & website
Nice to have
• Brand elements - some of them you may find in the attached Brand Guidelines (e.g. three lines on the background signifying "W")

```html
<!DOCTYPE html>
<html lang="en">
<head>
<meta charset="utf-8">
<title>Brovix – Business Cards</title>
<link rel="stylesheet" href="https://fonts.googleapis.com/css2?family=Lato:wght@400;700&display=swap">
<style>
  :root {
    --brand-green: #6cc000;
    --brand-green-text: #72c21a;
    --brand-grey: #3c3c3e;
    --band-black: #1b1b1b;
    --card-white: #ffffff;
    --stage: #ecebe7;
    --ink: #2a2a2a;
  }
  * { margin: 0; padding: 0; box-sizing: border-box; }
  html, body { width: 1200px; height: 800px; overflow: hidden; }
  body {
    background: var(--stage);
    font-family: "Lato", Arial, sans-serif;
    position: relative;
  }
  .card {
    position: absolute;
    top: 252px;
    width: 520px;
    height: 296px;
    border-radius: 4px;
    overflow: hidden;
    box-shadow: 0 6px 18px rgba(0,0,0,0.12);
  }
  /* Front */
  .card-front { left: 50px; background: var(--brand-green); }
  .card-front .wordmark {
    position: absolute; left: 56px; top: 118px;
    display: flex; align-items: center; gap: 12px;
    font-size: 54px; font-weight: 400; color: var(--brand-grey);
    letter-spacing: -1px;
  }
  .wordmark .dot {
    width: 22px; height: 22px; border-radius: 50%; background: currentColor;
  }
  .card-front .site {
    position: absolute; right: 24px; bottom: 26px;
    font-size: 15px; font-weight: 700; color: var(--card-white);
  }
  /* Back */
  .card-back { left: 630px; background: var(--card-white); }
  .holder { position: absolute; left: 36px; top: 34px; }
  .holder .name { font-size: 24px; font-weight: 400; color: var(--ink); }
  .holder .role { font-size: 15px; color: var(--brand-green-text); margin-top: 2px; }
  .contacts {
    position: absolute; left: 36px; top: 118px;
    list-style: none; font-size: 13px; color: var(--ink); line-height: 1.35;
  }
  .contacts li { display: flex; gap: 8px; align-items: flex-start; margin-bottom: 6px; }
  .contacts svg { flex: none; margin-top: 2px; }
  .card-back .wordmark {
    position: absolute; right: 34px; top: 70px;
    display: flex; align-items: center; gap: 10px;
    font-size: 40px; font-weight: 400; color: var(--brand-grey);
  }
  .card-back .wordmark .dot { width: 16px; height: 16px; background: var(--brand-green); }
  .band {
    position: absolute; left: 0; right: 0; top: 214px; height: 48px;
    background: linear-gradient(90deg, var(--band-black) 0%, var(--band-black) 78%, #4a4a4a 100%);
  }
  .band .site {
    position: absolute; right: 22px; top: 15px;
    font-size: 14px; color: var(--brand-green-text); letter-spacing: 0.5px;
  }
  .band .site strong { font-weight: 700; }
</style>
</head>
<body>
  <section class="card card-front" aria-label="Business card front">
    <div class="wordmark"><span class="dot"></span>brovix</div>
    <div class="site">www.brovix.example</div>
  </section>

  <section class="card card-back" aria-label="Business card back">
    <div class="holder">
      <div class="name">Halyna Dorosh</div>
      <div class="role">Director of Marketing</div>
    </div>
    <ul class="contacts">
      <li>
        <svg width="10" height="13" viewBox="0 0 10 13" aria-hidden="true"><path d="M5 0a4.5 4.5 0 0 0-4.5 4.5C.5 8 5 13 5 13s4.5-5 4.5-8.5A4.5 4.5 0 0 0 5 0zm0 6.3a1.8 1.8 0 1 1 0-3.6 1.8 1.8 0 0 1 0 3.6z" fill="var(--brand-green)"/></svg>
        <span>20517 - 87 Ave. Edmonton,<br>AB, Canada. T6K 4N8</span>
      </li>
      <li>
        <svg width="10" height="13" viewBox="0 0 10 13" aria-hidden="true"><rect x="1" y="0.5" width="8" height="12" rx="1.5" fill="none" stroke="var(--brand-green)" stroke-width="1.3"/><circle cx="5" cy="10.3" r="0.8" fill="var(--brand-green)"/></svg>
        <span>780.555.0184</span>
      </li>
      <li>
        <svg width="11" height="11" viewBox="0 0 11 11" aria-hidden="true"><rect x="0.7" y="2" width="9.6" height="7" rx="1" fill="none" stroke="var(--brand-green)" stroke-width="1.3"/><path d="M1 2.5l4.5 3.5L10 2.5" fill="none" stroke="var(--brand-green)" stroke-width="1.3"/></svg>
        <span>halya.dorosh@quillmail.example</span>
      </li>
    </ul>
    <div class="wordmark"><span class="dot"></span>brovix</div>
    <div class="band">
      <div class="site">www.<strong>brovix</strong>.example</div>
    </div>
  </section>
</body>
</html>
```